Business Card - connecting 2 souls and beggining the journey of self discovery

Logo on the front
with tag line

On the back list of services and contact details

Seminars
workshops
Coaching
podcasts

Darren Whitlow
Health & Wellbeing Life Coach
0491 372 615
darren@brightcoreliving.example
brightcoreliving.example

Industry/Entity Type

Life Coaching

Contact Information for Business Card

I like the use of colour from the logo to be used. I'm not a fan of white.

Requirements
Must have
• My tagline: The journey home starts with you
Nice to have
• Use of colour that is in the Brightcore Living logo

```html
<!DOCTYPE html>
<html lang="en">
<head>
<meta charset="utf-8">
<title>Brightcore Living – Business Card</title>
<link rel="stylesheet" href="https://fonts.googleapis.com/css2?family=Source+Sans+3:wght@300;400;600;700&display=swap">
<style>
  :root {
    --backdrop: #2b2b2c;
    --card: #141414;
    --card-edge: #1e1e1e;
    --accent: #f5a81c;
    --mark: #ee6a7a;
    --text: #ffffff;
    --muted: #8d8d8d;
    --rule: #2a2a2a;
  }
  * { margin: 0; padding: 0; box-sizing: border-box; }
  html, body {
    width: 1200px; height: 900px; overflow: hidden;
    background: var(--backdrop);
    font-family: "Source Sans 3", "Segoe UI", sans-serif;
    color: var(--text);
  }
  .stage {
    position: relative; width: 1200px; height: 900px;
    display: flex; align-items: center; justify-content: center; gap: 48px;
  }
  .card {
    position: relative; width: 520px; height: 310px;
    background: var(--card); border-radius: 22px;
    border: 1px solid var(--card-edge);
    box-shadow: 0 18px 40px rgba(0,0,0,.45);
  }
  .brand { display: flex; flex-direction: column; align-items: center; gap: 10px; }
  .brand-dot { width: 92px; height: 92px; border-radius: 50%; background: var(--mark); }
  .brand-name { font-size: 16px; font-weight: 600; color: var(--text); letter-spacing: .5px; }

  .card-contact .brand { position: absolute; left: 34px; top: 70px; width: 160px; }
  .card-contact .divider {
    position: absolute; left: 222px; top: 40px; width: 1px; height: 160px; background: var(--rule);
  }
  .person { position: absolute; left: 248px; top: 44px; }
  .person-name { font-size: 24px; font-weight: 700; color: var(--accent); line-height: 1.1; }
  .person-role { font-size: 14px; margin-top: 4px; }
  .contact-list { list-style: none; margin-top: 26px; }
  .contact-list li { display: flex; align-items: center; gap: 9px; font-size: 15px; line-height: 22px; }
  .contact-icon { width: 12px; height: 12px; flex: none; }
  .contact-icon .fill { fill: var(--accent); }
  .contact-icon .cut { fill: none; stroke: var(--card); stroke-width: 2; }

  .services {
    position: absolute; left: 34px; right: 30px; bottom: 34px;
    display: flex; align-items: center; justify-content: space-between;
    list-style: none; font-size: 17px; font-weight: 600;
  }
  .services .dot { width: 7px; height: 7px; border-radius: 50%; background: var(--accent); }

  .card-tagline { display: flex; flex-direction: column; align-items: center; justify-content: center; gap: 30px; }
  .tagline { font-size: 28px; font-weight: 400; color: var(--muted); letter-spacing: -.3px; white-space: nowrap; }
</style>
</head>
<body>
<main class="stage">
  <section class="card card-contact">
    <div class="brand">
      <span class="brand-dot"></span>
      <span class="brand-name">Brightcore Living</span>
    </div>
    <span class="divider"></span>
    <div class="person">
      <h1 class="person-name">Darren Whitlow</h1>
      <p class="person-role">Health &amp; Wellbeing Life Coach</p>
      <ul class="contact-list">
        <li><svg class="contact-icon" viewBox="0 0 24 24"><path class="fill" d="M6.6 10.8a15.1 15.1 0 0 0 6.6 6.6l2.2-2.2a1 1 0 0 1 1-.25 11.4 11.4 0 0 0 3.6.57 1 1 0 0 1 1 1V20a1 1 0 0 1-1 1A17 17 0 0 1 3 4a1 1 0 0 1 1-1h3.5a1 1 0 0 1 1 1c0 1.25.2 2.45.57 3.57a1 1 0 0 1-.25 1z"/></svg>0491 372 615</li>
        <li><svg class="contact-icon" viewBox="0 0 24 24"><rect class="fill" x="2" y="5" width="20" height="14" rx="1.5"/><polyline class="cut" points="3,6 12,13 21,6"/></svg>darren@brightcoreliving.example</li>
        <li><svg class="contact-icon" viewBox="0 0 24 24"><circle class="fill" cx="12" cy="12" r="10"/><path class="cut" d="M2 12h20M12 2c3 3 3 17 0 20M12 2c-3 3-3 17 0 20"/></svg>www.brightcoreliving.example</li>
      </ul>
    </div>
    <ul class="services">
      <li>Seminars</li><li class="dot"></li>
      <li>Workshops</li><li class="dot"></li>
      <li>Coaching</li><li class="dot"></li>
      <li>Podcasts</li>
    </ul>
  </section>

  <section class="card card-tagline">
    <div class="brand">
      <span class="brand-dot"></span>
      <span class="brand-name">Brightcore Living</span>
    </div>
    <p class="tagline">The journey home starts with you</p>
  </section>
</main>
</body>
</html>
```